Equipment Finance Specialist I work with companies who need the funds to buy their equipment

I would like a business card that stands out on the shelves. I want to be able to hand it to someone and say WOW. This card should have my logo.
You can put color into it I am very open on design and color

What my company does is we deal with dealerships that sell equipment such as Dump Trucks garbage trucks tractors trailers. Customers get referred to us and depending on their time in business we will ask for the following items

Companies that have been in business for more than two years we have a credit application program up to 250K . With this program we need the following items Credit application filled out(which is what I would like to be able for the customer to click on my website to get.) as well as three current month bank statements.

Deals over 250k we will need the following items

2 years business tax returns
2 years personal tax returns
Profit & Loss statement
Personal Financial Statement

what we do
100% FINANCING
SEASONAL PAYMENTS
LOAN BALLOON PAYMENTS
TRAC LEASING
LOW-INTEREST REFINANCING RATES
DEBT CONSOLIDATION

We specialize in creative financing solutions and offer a variety of reliable, flexible and expandable lending choices.

Target Market(s)

Trucking Companies

Industry/Entity Type

Trucking Company

Contact Information for Business Card

* $250,000 Application only Program
* Loans from $30,000 to 5,000,000
* Competitive Interest Rates

Font styles to use
Serif
Sans Serif

Colors

Designer to choose colors to be used in the design.

Requirements
Must have
• On the back of the card.
• * $250,000 Application only Program
• * Loans from $30,000 to 5,000,000
• My name, email, website. address
• * Competitive Interest Rates
• * 100% Financing
Nice to have
• I want my logo to pop on the card
• My logo is the great one I would like to use
Should not have
• I am up for your creativity as well

```html
<!DOCTYPE html>
<html lang="en">
<head>
<meta charset="UTF-8">
<title>Summit Haul Capital — Business Card</title>
<link href="https://fonts.googleapis.com/css2?family=Work+Sans:wght@400;500;800&display=swap" rel="stylesheet">
<style>
  :root {
    --backdrop: #202124;
    --card-navy: #1f2f6e;
    --emboss: #2b3d85;
    --silver: #e6e8ef;
    --silver-soft: #c9cdd9;
  }
  * { margin: 0; padding: 0; box-sizing: border-box; }
  html, body {
    width: 1200px; height: 900px; overflow: hidden;
    background: var(--backdrop);
    font-family: "Work Sans", Arial, sans-serif;
  }
  .canvas { position: relative; width: 1200px; height: 900px; }
  .card {
    position: absolute; left: 260px; width: 680px; height: 389px;
    background: var(--card-navy);
    box-shadow: 0 10px 30px rgba(0,0,0,0.45);
  }
  .card--front { top: 46px; }
  .card--back { top: 465px; }

  .brand { position: absolute; display: flex; align-items: center; gap: 16px; }
  .brand__dot {
    width: 64px; height: 64px; border-radius: 50%;
    border: 3px solid currentColor; flex: none;
  }
  .brand__name {
    font-weight: 800; font-size: 34px; line-height: 1.02;
    letter-spacing: 1px; text-transform: uppercase;
  }
  .card--front .brand {
    left: 50%; top: 46%; transform: translate(-50%, -50%);
    color: var(--silver);
  }
  .card--back .brand { left: 40px; top: 136px; color: var(--emboss); }
  .card--back .brand__name { font-size: 28px; }
  .card--back .brand__dot { width: 54px; height: 54px; }

  .offers {
    position: absolute; left: 40px; top: 214px; list-style: none;
    color: var(--silver-soft);
  }
  .offers__item {
    font-size: 12px; line-height: 1.75; letter-spacing: 0.6px;
    text-transform: uppercase; display: flex; align-items: center; gap: 8px;
  }
  .offers__item::before {
    content: ""; width: 5px; height: 5px; background: var(--silver-soft); flex: none;
  }

  .divider {
    position: absolute; left: 352px; top: 140px;
    width: 2px; height: 170px; background: var(--silver-soft);
  }
  .contact { position: absolute; left: 392px; top: 146px; color: var(--silver); }
  .contact__name {
    font-size: 26px; font-weight: 500; letter-spacing: 1.5px;
    text-transform: uppercase;
  }
  .contact__role { font-size: 14px; color: var(--silver-soft); margin-top: 2px; }
  .contact__address { font-size: 16px; line-height: 1.4; margin-top: 22px; letter-spacing: 0.8px; }
  .contact__list { list-style: none; margin-top: 14px; }
  .contact__item {
    display: flex; align-items: center; gap: 12px;
    font-size: 17px; line-height: 1.5; letter-spacing: 0.6px;
  }
  .contact__icon { width: 12px; height: 12px; flex: none; }
</style>
</head>
<body>
<div class="canvas">

  <section class="card card--front" aria-label="Card front">
    <div class="brand">
      <span class="brand__dot"></span>
      <span class="brand__name">Summit Haul<br>Capital</span>
    </div>
  </section>

  <section class="card card--back" aria-label="Card back">
    <div class="brand">
      <span class="brand__dot"></span>
      <span class="brand__name">Summit Haul<br>Capital</span>
    </div>

    <ul class="offers">
      <li class="offers__item">$250,000 Application Only Program</li>
      <li class="offers__item">Loans from $30,000 to $5,000,000</li>
      <li class="offers__item">Competitive Interest Rates</li>
      <li class="offers__item">100% Financing</li>
    </ul>

    <div class="divider"></div>

    <div class="contact">
      <p class="contact__name">Daniel Harper</p>
      <p class="contact__role">Director</p>
      <p class="contact__address">1180 Ridgeway Dr.<br>Garland, TX 75040</p>
      <ul class="contact__list">
        <li class="contact__item">
          <svg class="contact__icon" viewBox="0 0 12 12" aria-hidden="true"><path d="M2 1 L4.5 1 L5.5 3.5 L4 4.5 Q5 7 7.5 8 L8.5 6.5 L11 7.5 L11 10 Q6 11.5 2.5 7 Q0.5 4 2 1 Z" fill="var(--silver)"/></svg>
          1300 472 615
        </li>
        <li class="contact__item">
          <svg class="contact__icon" viewBox="0 0 12 12" aria-hidden="true"><rect x="0.75" y="2.25" width="10.5" height="7.5" fill="none" stroke="var(--silver)" stroke-width="1.2"/><path d="M1 2.5 L6 6.5 L11 2.5" fill="none" stroke="var(--silver)" stroke-width="1.2"/></svg>
          info@summithaul.com
        </li>
        <li class="contact__item">
          <svg class="contact__icon" viewBox="0 0 12 12" aria-hidden="true"><circle cx="6" cy="6" r="5" fill="none" stroke="var(--silver)" stroke-width="1.1"/><ellipse cx="6" cy="6" rx="2.2" ry="5" fill="none" stroke="var(--silver)" stroke-width="1"/><path d="M1 6 H11" stroke="var(--silver)" stroke-width="1"/></svg>
          www.summithaul.com
        </li>
      </ul>
    </div>
  </section>

</div>
</body>
</html>
```